Budget Brand Responsive Website

Flat vector style website needed for value based IT support company. looking for clean, illustration intensive based design. Current test site can be found at www.bright-mend.co.uk and holding page it www.brightmend.co.uk this will show text and services, please feel free to use placeholder text if you think we need alternative text in places. Emphasis should be on low cost support and services listed on the site, would be nice to see costs in bold images. important colors are the blue, orange and white, see holding page and attached image of an advert

It Company

```html
<!DOCTYPE html>
<html lang="en">
<head>
<meta charset="utf-8">
<title>Bright Mend – Low Cost IT Support</title>
<link href="https://fonts.googleapis.com/css2?family=Oswald:wght@400;500&family=Open+Sans:wght@400;600;700&display=swap" rel="stylesheet">
<style>
:root{
  --blue:#2f5196;
  --navy:#1f3a6e;
  --hero-text:#24385f;
  --orange:#e3892b;
  --white:#ffffff;
  --grey-bg:#f1f2f4;
  --line:#dfe2e8;
  --text:#555b66;
  --heading:#2b2f36;
  --icon:#8a909a;
  --form-bg:#e9ebee;
}
*{box-sizing:border-box;margin:0;padding:0}
html,body{width:1200px;height:3252px;overflow:hidden}
body{font-family:"Open Sans",Arial,sans-serif;color:var(--text);background:var(--white);font-size:15px;line-height:1.6}
h2,h3,.label{font-family:"Oswald","Arial Narrow",sans-serif;font-weight:400;color:var(--heading)}
.section-title{font-size:30px;text-align:center;text-transform:uppercase;letter-spacing:.5px}
.section-title::after{content:"";display:block;width:60px;height:3px;background:var(--orange);margin:10px auto 0}
.btn{display:inline-block;font-family:"Open Sans",sans-serif;font-size:13px;font-weight:600;color:var(--white);background:var(--orange);padding:10px 30px;text-transform:uppercase}
.btn.blue{background:var(--blue)}

.site-header{height:60px;display:flex;align-items:center;justify-content:space-between;padding:0 100px}
.brand{display:flex;align-items:center;gap:12px;font-family:"Oswald",sans-serif;font-size:30px;font-weight:500;color:var(--blue)}
.brand-dot{width:22px;height:22px;background:var(--orange)}
.nav{display:flex;gap:4px;font-size:12px;font-weight:600;text-transform:uppercase}
.nav a{padding:10px 18px;color:var(--text);text-decoration:none}
.nav a.active{background:var(--orange);color:var(--white)}

.hero{position:relative;height:540px;background:linear-gradient(90deg,#5c6b80 0%,#c9ced6 35%,#e6e8ec 60%,#d4d8de 100%)}
.hero-text{position:absolute;right:130px;top:330px;text-align:right;font-size:38px;line-height:1.2;color:var(--hero-text);font-weight:600}
.hero-text b{font-weight:700;color:var(--navy)}
.hero-arrow{position:absolute;top:250px;width:40px;height:40px;border-radius:50%;background:rgba(255,255,255,.85)}
.hero-arrow.left{left:20px}.hero-arrow.right{right:20px}

.welcome{height:440px;padding:60px 100px 0;text-align:center}
.welcome .lead{font-size:24px;font-weight:600;color:var(--heading);margin:14px 0 14px}
.welcome p{font-size:14px;text-align:left;margin-bottom:34px}

.features{height:460px;padding:0 100px}
.feature-grid{display:grid;grid-template-columns:repeat(3,1fr);gap:60px;margin-top:50px}
.feature{border:1px solid var(--line);height:120px;padding:26px 22px 0 90px;position:relative;font-size:12px;line-height:1.5}
.feature .label{position:absolute;left:90px;top:10px;font-size:14px;text-transform:uppercase}
.feature .ico{position:absolute;left:26px;top:26px;width:44px;height:44px}
.feature p{margin-top:20px}
.feature.active{background:var(--blue);color:#dfe6f5;border-color:var(--blue)}
.feature.active .label{color:var(--white)}

.band{height:300px;background:var(--blue);color:#dbe3f4;text-align:center;padding:50px 140px 0}
.band .section-title{color:var(--white)}
.band p{font-size:13px;margin:24px 0 14px}
.band .call{font-family:"Oswald",sans-serif;font-size:24px;color:var(--white);display:flex;align-items:center;justify-content:center;gap:12px;margin-top:10px}

.pricing{height:560px;background:var(--grey-bg);padding:50px 100px 0}
.plans{display:grid;grid-template-columns:repeat(4,1fr);gap:30px;margin-top:50px}
.plan{background:var(--white);height:330px;padding:24px 20px;text-align:center}
.plan h3{font-size:24px;text-transform:uppercase}
.plan .sub{font-weight:600;font-size:14px;color:var(--heading);margin:6px 0 18px;min-height:44px;line-height:1.4}
.plan ul{list-style:none;font-size:13px;margin-bottom:22px}
.plan li{border-top:1px solid var(--line);padding:9px 0}
.plan li b{color:var(--heading)}

.values{height:360px;padding:50px 100px 0;text-align:center}
.values p{font-size:13px;margin:24px 0 40px}
.value-row{display:flex;justify-content:space-between;padding:0 20px}
.value{width:160px;font-family:"Oswald",sans-serif;font-size:17px;color:var(--heading)}
.value svg{display:block;margin:0 auto 14px}

.contact{height:470px;padding:50px 100px 0}
.contact .intro{font-size:13px;text-align:center;margin:22px 100px 40px}
.contact-body{display:flex;gap:60px;padding-left:60px}
.contact-info{width:240px;font-size:13px}
.contact-info dt{font-family:"Oswald",sans-serif;text-transform:uppercase;color:var(--icon);letter-spacing:1.5px;font-size:12px;margin-top:14px}
.contact-info dd{color:var(--heading)}
.form-wrap{flex:1}
.form{background:var(--form-bg);padding:30px;display:grid;grid-template-columns:1fr 1fr;gap:14px 20px;height:220px}
.form .col{display:flex;flex-direction:column;gap:14px}
.field{background:var(--white);height:36px;font-size:12px;color:#999;padding:8px 12px}
.field.area{height:86px}
.form .btn{text-align:center}
.form-note{font-size:11px;margin-top:10px}

.site-footer{height:62px;background:var(--navy);color:#c8d2e6;font-size:12px;display:flex;align-items:center;justify-content:space-between;padding:0 40px}
.social{display:flex;gap:10px}
.social span{width:24px;height:24px;border-radius:50%;background:var(--orange)}
.social span:nth-child(2){background:#3e6bc0}
.social span:nth-child(3){background:#4a8fd6}
.social span:nth-child(4){background:#2e5aa6}
</style>
</head>
<body>

<header class="site-header">
  <div class="brand"><span class="brand-dot"></span>BRIGHT MEND</div>
  <nav class="nav"><a class="active">Home</a><a>Support</a><a>Services</a><a>About</a><a>Contact</a></nav>
</header>

<section class="hero" role="img" aria-label="Photo of a smiling businessman in a suit in a bright office with colleagues behind">
  <span class="hero-arrow left"><svg width="40" height="40"><path d="M23 13l-7 7 7 7" stroke="#555" stroke-width="2.5" fill="none"/></svg></span>
  <span class="hero-arrow right"><svg width="40" height="40"><path d="M17 13l7 7-7 7" stroke="#555" stroke-width="2.5" fill="none"/></svg></span>
  <div class="hero-text">We Offer <b>low cost</b><br>support and services</div>
</section>

<section class="welcome">
  <h2 class="section-title">Welcome</h2>
  <div class="lead">Lorem ipsum dolor sit amet</div>
  <p>Bright Mend is a trusted IT support provider for small firms across the region. We give clear advice, fast fixes and fair prices, so your team can get on with work while we keep systems safe, stable and up to date. Our support plans grow with you, with no hidden fees and no long contracts to sign.</p>
  <span class="btn">Read More</span>
</section>

<section class="features">
  <h2 class="section-title">Services Tailored For You</h2>
  <div class="feature-grid">
    <div class="feature active"><svg class="ico" viewBox="0 0 44 44"><rect x="6" y="8" width="32" height="22" fill="none" stroke="#fff" stroke-width="2.5"/><path d="M16 36h12M22 30v6" stroke="#fff" stroke-width="2.5"/></svg><span class="label">Support</span><p>Short text about this service goes here for your team to read.</p></div>
    <div class="feature"><svg class="ico" viewBox="0 0 44 44"><path d="M12 8l6 0 3 8-4 3c2 4 5 7 9 9l3-4 8 3v6c-14 1-26-11-25-25z" fill="#8a909a"/></svg><span class="label">Voice</span><p>Short text about this service goes here for your team to read.</p></div>
    <div class="feature"><svg class="ico" viewBox="0 0 44 44"><circle cx="22" cy="22" r="15" fill="none" stroke="#8a909a" stroke-width="2.5"/><path d="M7 22h30M22 7c-8 9-8 21 0 30M22 7c8 9 8 21 0 30" fill="none" stroke="#8a909a" stroke-width="2"/></svg><span class="label">Internet</span><p>Short text about this service goes here for your team to read.</p></div>
    <div class="feature"><svg class="ico" viewBox="0 0 44 44"><rect x="10" y="20" width="24" height="18" fill="#8a909a"/><path d="M15 20v-6a7 7 0 0 1 14 0v6" fill="none" stroke="#8a909a" stroke-width="3"/></svg><span class="label">Security</span><p>Short text about this service goes here for your team to read.</p></div>
    <div class="feature"><svg class="ico" viewBox="0 0 44 44"><rect x="8" y="8" width="28" height="10" fill="#8a909a"/><rect x="8" y="22" width="28" height="10" fill="#8a909a"/><circle cx="30" cy="13" r="2" fill="#fff"/><circle cx="30" cy="27" r="2" fill="#fff"/></svg><span class="label">Hosting</span><p>Short text about this service goes here for your team to read.</p></div>
    <div class="feature"><svg class="ico" viewBox="0 0 44 44"><path d="M12 32a8 8 0 0 1 1-16 10 10 0 0 1 19 2 7 7 0 0 1 0 14z" fill="#8a909a"/></svg><span class="label">Cloud</span><p>Short text about this service goes here for your team to read.</p></div>
  </div>
</section>

<section class="band">
  <h2 class="section-title">Services Tailored For You</h2>
  <p>We don't believe any small business should pay for IT support you don't need. Our simple plans are built around what you actually use, and every plan comes with friendly help from real people. Whether you need one laptop fixed or a full office setup, we have it covered.</p>
  <p>Want to learn how other businesses are saving with Bright Mend?</p>
  <div class="call"><svg width="26" height="26" viewBox="0 0 44 44"><path d="M12 8l6 0 3 8-4 3c2 4 5 7 9 9l3-4 8 3v6c-14 1-26-11-25-25z" fill="#fff"/></svg>CALL US TODAY ON 01632 960 418</div>
</section>

<section class="pricing">
  <h2 class="section-title">Services Tailored For You</h2>
  <div class="plans">
    <div class="plan"><h3>Support</h3><div class="sub">Unlimited Monthly Remote Support</div><ul><li>Workstations <b>£8.50</b></li><li>Client PC <b>£20.00</b></li><li>Servers <b>£49.00</b></li></ul><span class="btn">More</span></div>
    <div class="plan"><h3>Voice</h3><div class="sub">Lower Rates And Call Charges</div><ul><li>PBX from <b>£49.00</b></li><li>Line rental from <b>£9.99</b></li><li>Phone numbers from <b>£5.00</b></li></ul><span class="btn blue">More</span></div>
    <div class="plan"><h3>Hosting</h3><div class="sub">Flexible And Secure</div><ul><li>Email hosting from <b>£2.00</b></li><li>Email protection from <b>£1.00</b></li><li>Office apps from <b>£3.50</b></li></ul><span class="btn blue">More</span></div>
    <div class="plan"><h3>Cloud</h3><div class="sub">Reduce Costs &amp; Increase Performance</div><ul><li>Online Backup</li><li>Private Cloud Servers</li><li>Virtual Desktop</li></ul><span class="btn blue">More</span></div>
  </div>
</section>

<section class="values">
  <h2 class="section-title">We Make It Simple &amp; Fairer</h2>
  <p>Some pricing should be simple, which is why we keep things plain and honest. Our plans are clear, our support is quick and our team uses the latest tools to keep you running. No catches, no fine print, just help when you need it.</p>
  <div class="value-row">
    <div class="value"><svg width="44" height="44" viewBox="0 0 44 44"><rect x="5" y="5" width="34" height="34" fill="none" stroke="var(--orange)" stroke-width="2.5"/><path d="M13 22l6 6 12-13" stroke="var(--orange)" stroke-width="3" fill="none"/></svg>Fair Pricing</div>
    <div class="value"><svg width="44" height="44" viewBox="0 0 44 44"><rect x="10" y="5" width="24" height="34" fill="none" stroke="var(--orange)" stroke-width="2.5"/><path d="M15 16l14 14M29 16L15 30" stroke="var(--orange)" stroke-width="2.5"/></svg>No Contracts</div>
    <div class="value"><svg width="44" height="44" viewBox="0 0 44 44"><circle cx="22" cy="22" r="16" fill="none" stroke="var(--orange)" stroke-width="2.5"/><path d="M22 12v10l7 5" stroke="var(--orange)" stroke-width="2.5" fill="none"/></svg>Fast Response</div>
    <div class="value"><svg width="44" height="44" viewBox="0 0 44 44"><rect x="6" y="8" width="32" height="22" fill="none" stroke="var(--orange)" stroke-width="2.5"/><path d="M16 36h12M22 30v6" stroke="var(--orange)" stroke-width="2.5"/></svg>Latest Technology</div>
    <div class="value"><svg width="44" height="44" viewBox="0 0 44 44"><circle cx="22" cy="22" r="16" fill="none" stroke="var(--orange)" stroke-width="2.5"/><path d="M14 25c3 5 13 5 16 0" stroke="var(--orange)" stroke-width="2.5" fill="none"/><circle cx="16" cy="17" r="2" fill="var(--orange)"/><circle cx="28" cy="17" r="2" fill="var(--orange)"/></svg>Satisfied Customers</div>
  </div>
</section>

<section class="contact">
  <h2 class="section-title">Contact Us</h2>
  <p class="intro">Drop us a line with your question and a member of our team will get back to you within one working day.</p>
  <div class="contact-body">
    <dl class="contact-info">
      <dt>Call Me</dt><dd>+44 (0) 1632 960 418</dd>
      <dt>Email Me</dt><dd>sales@brightmend.co.uk</dd>
      <dt>Address</dt><dd>Bright Mend Solutions Ltd trading as Bright Mend. Company registered in England and Wales.</dd>
    </dl>
    <div class="form-wrap">
      <div class="form">
        <div class="col"><div class="field">Name</div><div class="field">Email</div><div class="field">Subject</div></div>
        <div class="col"><div class="field area">Message</div><span class="btn">Send Now</span></div>
      </div>
      <div class="form-note">Fields marked * are required</div>
    </div>
  </div>
</section>

<footer class="site-footer">
  <span>Copyright © 2015 your site. All rights reserved</span>
  <div class="social"><span></span><span></span><span></span><span></span></div>
</footer>

</body>
</html>
```